International Film making Business needs the 5 Logos provided made into a POSTER Format

Design Task:
CREATE A POSTER DESIGN USING THE 5 LOGOS PROVIDED. The BOLD BRIGHT HORIZON LOGO should stand out from the others by being in the middle with the other 4 logos connected to it somehow.

The 5 Businesses already has their 5 Logos, all similar in design to each other.

BOLD BRIGHT HORIZON is the Main Logo that encompasses the other 4 Logos. So it must stand out more and it is like the Overall Business entity that incorporates the other 4 Logos.

What is required is that by using the 5 Logo designs provided, create a cool graphic artwork that somehow incorporates ALL of the 5 Logos - But having the BOLD BRIGHT HORIZON Logo at the forefront/most important/standing out the most.
- BOLD BRIGHT HORIZON will probably be bigger than the others
- and could be changed into 3D.

I have attached all 5 logos and a hand drawn example of how the BOLD BRIGHT HORIZONS could stand out from the rest.

THE DESIGNS OF THE LOGOS SHOULD NOT BE CHANGED (except the BOLDBRIGHTHORIZON which can be 3D)

Please do not be restricted with the sample idea. Creativity is encouraged

DIMENSION: 3000 mm x 6000 mm
high resolution graphic

Logo Text

bold bright , bold bright pictures, bold bright legends, bold bright groovy, BOLD BRIGHT HORIZONS

Requirements
Must have
• USE THE 5 LOGOS PROVIDED ONLY - Only BOLD BRIGHT HORIZON can be changed into 3D only
Nice to have
• Eye catching design, showing the Bold Bright Horizon as the most powerful Logo that has the other 4 as subordinate companies
Should not have
• ANY CHANGE IN THE 5 LOGO DESIGNS (EXcept 3D for Bold Bright Horizons)

```html
<!DOCTYPE html>
<html lang="en">
<head>
<meta charset="utf-8">
<title>Bold Bright Horizons – Poster</title>
<link rel="stylesheet" href="https://fonts.googleapis.com/css2?family=Cinzel:wght@600;700&family=Montserrat:wght@300&display=swap">
<style>
  :root {
    --gold-dark: #b5852e;
    --gold-light: #f6e6a6;
    --gold-mid: #d9b867;
    --white: #ffffff;
    --green: #1f8a3a;
    --legend-purple: #6a2c91;
    --picture-grey: #3a3a3a;
    --bright-blue: #1f7fc4;
    --main-gold: #bd8d35;
    --web-grey: #6d6d6d;
  }
  html, body {
    margin: 0;
    padding: 0;
    width: 1200px;
    height: 600px;
    overflow: hidden;
    background: var(--white);
  }
  .poster {
    display: block;
    width: 1200px;
    height: 600px;
  }
  .brand-name {
    font-family: "Cinzel", serif;
    font-weight: 700;
    text-anchor: middle;
  }
  .brand-name--groovy { fill: var(--green); }
  .brand-name--legends { fill: var(--legend-purple); }
  .brand-name--pictures { fill: var(--picture-grey); }
  .brand-name--bright { fill: var(--bright-blue); }
  .main-name {
    font-family: "Cinzel", serif;
    font-weight: 700;
    fill: var(--main-gold);
    letter-spacing: 4px;
  }
  .main-web {
    font-family: "Montserrat", sans-serif;
    font-weight: 300;
    fill: var(--web-grey);
    letter-spacing: 6px;
  }
</style>
</head>
<body>
<svg class="poster" viewBox="0 0 2560 1280" xmlns="http://www.w3.org/2000/svg" aria-label="Bold Bright Horizons brand family poster">
  <defs>
    <linearGradient id="band-green" x1="0" x2="1" y1="0" y2="0">
      <stop offset="0" stop-color="#066b3a"/>
      <stop offset="0.5" stop-color="#7fbf3f"/>
      <stop offset="1" stop-color="#066b3a"/>
    </linearGradient>
    <linearGradient id="band-rainbow" x1="0" x2="1" y1="0" y2="0">
      <stop offset="0" stop-color="#f04e23"/>
      <stop offset="0.15" stop-color="#fff200"/>
      <stop offset="0.32" stop-color="#39b54a"/>
      <stop offset="0.5" stop-color="#2e3192"/>
      <stop offset="0.7" stop-color="#2b2162"/>
      <stop offset="1" stop-color="#662d91"/>
    </linearGradient>
    <linearGradient id="band-black" x1="0" x2="1" y1="0" y2="0">
      <stop offset="0" stop-color="#000000"/>
      <stop offset="0.45" stop-color="#8a8a8c"/>
      <stop offset="1" stop-color="#000000"/>
    </linearGradient>
    <linearGradient id="band-blue" x1="0" x2="1" y1="0" y2="0">
      <stop offset="0" stop-color="#27449a"/>
      <stop offset="0.5" stop-color="#1aaee5"/>
      <stop offset="1" stop-color="#27449a"/>
    </linearGradient>
    <linearGradient id="gold-field" x1="0" y1="0" x2="1" y2="1">
      <stop offset="0" stop-color="var(--gold-dark)"/>
      <stop offset="0.3" stop-color="var(--gold-mid)"/>
      <stop offset="0.45" stop-color="var(--gold-dark)"/>
      <stop offset="1" stop-color="var(--gold-dark)"/>
    </linearGradient>
    <linearGradient id="gold-frame" x1="0" y1="1" x2="1" y2="0">
      <stop offset="0" stop-color="var(--gold-dark)"/>
      <stop offset="0.35" stop-color="var(--gold-light)"/>
      <stop offset="0.6" stop-color="var(--gold-dark)"/>
      <stop offset="1" stop-color="var(--gold-dark)"/>
    </linearGradient>
    <radialGradient id="mark-disc" cx="0.4" cy="0.4" r="0.7">
      <stop offset="0" stop-color="#f3e3a8"/>
      <stop offset="1" stop-color="var(--main-gold)"/>
    </radialGradient>
  </defs>

  <!-- colour bands -->
  <g class="bands">
    <rect x="267" y="0" width="530" height="540" fill="url(#band-green)"/>
    <rect x="795" y="0" width="497" height="540" fill="url(#band-rainbow)"/>
    <rect x="1290" y="0" width="499" height="540" fill="url(#band-black)"/>
    <rect x="1787" y="0" width="523" height="540" fill="url(#band-blue)"/>
  </g>

  <!-- gold base -->
  <rect class="gold-base" x="267" y="540" width="2043" height="740" fill="url(#gold-field)"/>

  <!-- central white diamond -->
  <polygon class="main-diamond" points="545,507 791,272 1786,272 2031,507 1288,1250" fill="var(--white)"/>
  <polyline class="main-diamond-frame" points="545,520 1288,1263 2031,520" fill="none" stroke="url(#gold-frame)" stroke-width="36"/>

  <!-- brand diamonds -->
  <g class="brand-diamond brand-diamond--groovy">
    <polygon points="542,4 810,272 542,540 274,272" fill="url(#gold-frame)"/>
    <polygon points="542,50 764,272 542,494 320,272" fill="var(--white)"/>
    <circle cx="542" cy="200" r="36" fill="var(--green)"/>
    <text class="brand-name brand-name--groovy" x="542" y="300" font-size="46">BOLD BRIGHT</text>
    <text class="brand-name brand-name--groovy" x="542" y="366" font-size="62">GROOVY</text>
  </g>
  <g class="brand-diamond brand-diamond--legends">
    <polygon points="1040,4 1308,272 1040,540 772,272" fill="url(#gold-frame)"/>
    <polygon points="1040,50 1262,272 1040,494 818,272" fill="var(--white)"/>
    <circle cx="1040" cy="200" r="36" fill="var(--legend-purple)"/>
    <text class="brand-name brand-name--legends" x="1040" y="300" font-size="46">BOLD BRIGHT</text>
    <text class="brand-name brand-name--legends" x="1040" y="366" font-size="58">LEGENDS</text>
  </g>
  <g class="brand-diamond brand-diamond--pictures">
    <polygon points="1537,4 1805,272 1537,540 1269,272" fill="url(#gold-frame)"/>
    <polygon points="1537,50 1759,272 1537,494 1315,272" fill="var(--white)"/>
    <circle cx="1537" cy="200" r="36" fill="var(--picture-grey)"/>
    <text class="brand-name brand-name--pictures" x="1537" y="300" font-size="46">BOLD BRIGHT</text>
    <text class="brand-name brand-name--pictures" x="1537" y="362" font-size="52">PICTURES</text>
  </g>
  <g class="brand-diamond brand-diamond--bright">
    <polygon points="2033,4 2301,272 2033,540 1765,272" fill="url(#gold-frame)"/>
    <polygon points="2033,50 2255,272 2033,494 1811,272" fill="var(--white)"/>
    <circle cx="2033" cy="200" r="36" fill="var(--bright-blue)"/>
    <text class="brand-name brand-name--bright" x="2033" y="300" font-size="52">BOLD</text>
    <text class="brand-name brand-name--bright" x="2033" y="366" font-size="60">BRIGHT</text>
  </g>

  <!-- main brand -->
  <g class="main-brand">
    <circle cx="1050" cy="690" r="120" fill="url(#mark-disc)"/>
    <text class="main-name" x="1210" y="688" font-size="68" textLength="505" lengthAdjust="spacingAndGlyphs">BOLD BRIGHT</text>
    <text class="main-name" x="1210" y="778" font-size="68" textLength="505" lengthAdjust="spacingAndGlyphs">HORIZONS</text>
    <text class="main-web" x="1210" y="820" font-size="34" textLength="505" lengthAdjust="spacingAndGlyphs">boldbrighthorizons.net.au</text>
  </g>
</svg>
</body>
</html>
```